Birchline Septic Solutions

Would like to see some single sided ones but would also like to see some double sided with one sided only being the logo. Owners name is Colin Vandro. Phone number is 555-214-0387
Services are pumping, inspections, installs, and repairs

Contact Information for Business Card

555-241-0387 Colin Vandro Harlow Creek, OH

```html
<!DOCTYPE html>
<html lang="en">
<head>
<meta charset="utf-8">
<title>Birchline Septic Solutions – Business Card</title>
<link rel="stylesheet" href="https://fonts.googleapis.com/css2?family=Open+Sans:wght@400;600;700;800&display=swap">
<style>
  :root {
    --page-bg: #2a2a2c;
    --card-bg: #212124;
    --card-deep: #18181a;
    --scene-tone: #313236;
    --pattern-light: #6d6e72;
    --teal: #1fb8ac;
    --white: #ffffff;
    --text-soft: #e9e9ea;
  }
  * { box-sizing: border-box; margin: 0; padding: 0; }
  html, body {
    width: 1200px;
    height: 779px;
    overflow: hidden;
    background: var(--page-bg);
    font-family: "Open Sans", Arial, sans-serif;
  }
  .sheet {
    width: 1200px;
    height: 779px;
    display: flex;
    flex-direction: column;
    align-items: center;
    justify-content: center;
    gap: 28px;
  }
  .card {
    position: relative;
    width: 600px;
    height: 343px;
    background: var(--card-bg);
    overflow: hidden;
  }
  .card__edge {
    position: absolute;
    left: 0; right: 0; bottom: 0;
    height: 6px;
    background: var(--teal);
  }

  /* Front: logo side */
  .card--front { background: var(--card-deep); }
  .front__pattern {
    position: absolute;
    inset: 0 0 6px 0;
    background: linear-gradient(160deg, #101011 35%, #3a3b3e 70%, var(--pattern-light) 100%);
  }
  .front__brand {
    position: absolute;
    right: 48px;
    bottom: 34px;
    display: flex;
    align-items: center;
    gap: 8px;
    color: var(--white);
    font-weight: 700;
    font-size: 15px;
    letter-spacing: 0.02em;
  }
  .brand-dot {
    width: 10px; height: 10px;
    border-radius: 50%;
    background: var(--teal);
  }

  /* Back: contact side */
  .back__scene {
    position: absolute;
    left: 100px; top: 20px;
    width: 500px; height: 250px;
    background: radial-gradient(ellipse 60% 55% at 55% 55%, var(--scene-tone) 0%, rgba(49,50,54,0.6) 55%, rgba(49,50,54,0) 100%);
  }
  .back__brand {
    position: absolute;
    left: 40px;
    top: 120px;
    width: 235px;
    display: flex;
    align-items: center;
    gap: 10px;
    color: var(--white);
    font-weight: 800;
    font-size: 21px;
    line-height: 1.15;
  }
  .back__brand .brand-dot { flex: 0 0 14px; width: 14px; height: 14px; }
  .back__divider {
    position: absolute;
    left: 298px;
    top: 36px;
    width: 2px;
    height: 180px;
    background: var(--white);
  }
  .contact {
    position: absolute;
    left: 328px;
    top: 60px;
    color: var(--text-soft);
  }
  .contact__name {
    font-size: 30px;
    font-weight: 800;
    line-height: 1.1;
    color: var(--white);
  }
  .contact__first { color: var(--teal); }
  .contact__town {
    margin-top: 4px;
    font-size: 15px;
    font-weight: 600;
  }
  .contact__phone {
    margin-top: 4px;
    display: flex;
    align-items: center;
    gap: 8px;
    font-size: 16px;
    font-weight: 600;
  }
  .contact__phone svg { width: 15px; height: 15px; }
  .services {
    position: absolute;
    left: 0; right: 0;
    bottom: 34px;
    text-align: center;
  }
  .services__tag {
    display: inline-block;
    padding: 3px 22px;
    border-radius: 50%;
    background: var(--teal);
    color: var(--white);
    font-size: 13px;
    font-weight: 700;
    letter-spacing: 0.04em;
    margin-bottom: 10px;
  }
  .services__list {
    display: flex;
    justify-content: center;
    gap: 16px;
    list-style: none;
    color: var(--text-soft);
    font-size: 15px;
  }
  .services__list li {
    display: flex;
    align-items: center;
    gap: 7px;
  }
  .services__list li::before {
    content: "";
    width: 9px; height: 9px;
    border-radius: 50%;
    background: var(--teal);
  }
</style>
</head>
<body>
<main class="sheet">

  <section class="card card--front" aria-label="Card front">
    <div class="front__pattern" role="img" aria-label="Repeating pattern of mountain and pine silhouettes fading from black to grey"></div>
    <div class="front__brand"><span class="brand-dot"></span>Birchline Septic Solutions</div>
    <div class="card__edge"></div>
  </section>

  <section class="card card--back" aria-label="Card back">
    <div class="back__scene" role="img" aria-label="Faint mountain peak and pine tree silhouettes"></div>
    <div class="back__brand"><span class="brand-dot"></span>Birchline Septic Solutions</div>
    <div class="back__divider"></div>
    <div class="contact">
      <p class="contact__name"><span class="contact__first">Colin</span> Vandro</p>
      <p class="contact__town">Harlow Creek, OH</p>
      <p class="contact__phone">
        <svg viewBox="0 0 24 24" aria-hidden="true"><path fill="#1fb8ac" d="M6.6 10.8c1.4 2.8 3.8 5.1 6.6 6.6l2.2-2.2c.3-.3.7-.4 1-.2 1.1.4 2.3.6 3.6.6.6 0 1 .4 1 1V20c0 .6-.4 1-1 1C10.6 21 3 13.4 3 4c0-.6.4-1 1-1h3.5c.6 0 1 .4 1 1 0 1.3.2 2.5.6 3.6.1.3 0 .7-.2 1l-2.3 2.2z"/></svg>
        555-241-0387
      </p>
    </div>
    <div class="services">
      <span class="services__tag">SERVICES</span>
      <ul class="services__list">
        <li>Pumping</li>
        <li>Inspections</li>
        <li>Installs</li>
        <li>And Repairs</li>
      </ul>
    </div>
    <div class="card__edge"></div>
  </section>

</main>
</body>
</html>
```